RTavenor Business Cards & Letterhead

I have a logo but need a design for some new business cards. We are a Design-Build Firm that specializes in the design and construction of commercial projects.
the cards need to be professional. no cartoon stuff.
i would like to have the cards in AI format so I can update the card as needed. Logo is provided.
Our Address is: 4187 Marlowe Ct. Larkfield, Vermont 27614

```html
<!DOCTYPE html>
<html lang="en">
<head>
<meta charset="utf-8">
<title>RTavenor Business Cards</title>
<link href="https://fonts.googleapis.com/css2?family=Open+Sans:wght@400;600;700;800&display=swap" rel="stylesheet">
<style>
  :root {
    --bg: #333333;
    --card: #ffffff;
    --ink: #1a1a1a;
    --logo-grey: #58585a;
    --blue: #1b6fb5;
    --blue-dark: #0f4c8a;
    --band-grey: #555658;
    --wash: #d6deec;
    --wash-deep: #c9cfde;
  }
  * { margin: 0; padding: 0; box-sizing: border-box; }
  html, body { width: 1200px; height: 780px; overflow: hidden; }
  body {
    background: var(--bg);
    font-family: "Open Sans", Arial, sans-serif;
    display: flex;
    align-items: center;
    justify-content: center;
    gap: 40px;
  }
  .card {
    position: relative;
    width: 540px;
    height: 309px;
    background: var(--card);
    overflow: hidden;
    box-shadow: 0 10px 28px rgba(0,0,0,.45);
  }
  .wordmark {
    display: flex;
    align-items: center;
    gap: 8px;
    font-weight: 800;
    color: var(--logo-grey);
    letter-spacing: .5px;
    line-height: 1;
  }
  .wordmark__square { background: var(--blue); flex: none; }

  /* Back */
  .card--back { display: flex; align-items: center; justify-content: center; }
  .card--back .wordmark { font-size: 52px; gap: 12px; }
  .card--back .wordmark__square { width: 38px; height: 38px; }

  /* Front */
  .card--front .wordmark { position: absolute; left: 30px; top: 44px; font-size: 30px; }
  .card--front .wordmark__square { width: 22px; height: 22px; }
  .feature-panel {
    position: absolute; left: 330px; top: 20px; width: 210px; height: 250px;
    border-radius: 18px 0 0 60px;
    background: linear-gradient(160deg, var(--wash) 0%, var(--wash-deep) 100%);
    opacity: .75;
  }
  .nameplate { position: absolute; right: 28px; top: 110px; text-align: right; }
  .nameplate__name { color: var(--blue); font-weight: 700; font-size: 25px; letter-spacing: .5px; line-height: 1.1; }
  .nameplate__title { color: var(--ink); font-size: 14px; font-weight: 600; letter-spacing: .6px; }
  .name-tab { position: absolute; right: 0; top: 110px; width: 14px; height: 38px;
    background: radial-gradient(circle at 30% 50%, #2a8ee0, var(--blue-dark)); }
  .contact { position: absolute; left: 30px; top: 172px; color: var(--ink); font-size: 13.5px; line-height: 1.3; }
  .contact__address { margin-bottom: 8px; }
  .contact__row { display: flex; align-items: center; gap: 8px; }
  .contact__row svg { width: 13px; height: 13px; flex: none; }
  .footer-bands { position: absolute; left: 0; bottom: 0; width: 540px; height: 80px; }
</style>
</head>
<body>

<section class="card card--back" aria-label="Business card back">
  <div class="wordmark"><span class="wordmark__square"></span>RTAVENOR</div>
</section>

<section class="card card--front" aria-label="Business card front">
  <div class="feature-panel" role="img" aria-label="Faint brand decoration"></div>
  <div class="wordmark"><span class="wordmark__square"></span>RTAVENOR</div>

  <div class="name-tab"></div>
  <div class="nameplate">
    <p class="nameplate__name">ROWAN TAVENOR</p>
    <p class="nameplate__title">Founder/President</p>
  </div>

  <div class="contact">
    <p class="contact__address">4187 Marlowe Ct. Larkfield,<br>Vermont 27614</p>
    <p class="contact__row">
      <svg viewBox="0 0 16 16"><path fill="#1b6fb5" d="M4 1l2.5 3-1.5 2c1 2 3 4 5 5l2-1.5 3 2.5-1.5 2.5C8 15 1 8 1.5 3.5z"/></svg>
      (730) 555-0148
    </p>
    <p class="contact__row">
      <svg viewBox="0 0 16 16"><circle cx="8" cy="8" r="6.5" fill="none" stroke="#1b6fb5" stroke-width="1.6"/><path d="M1.5 8h13M8 1.5c-3 3.5-3 9.5 0 13M8 1.5c3 3.5 3 9.5 0 13" fill="none" stroke="#1b6fb5" stroke-width="1.2"/></svg>
      www.rtavenor.com
    </p>
    <p class="contact__row">
      <svg viewBox="0 0 16 16"><rect x="1" y="3.5" width="14" height="10" rx="1" fill="none" stroke="#1b6fb5" stroke-width="1.6"/><path d="M1.5 4.5l6.5 5 6.5-5" fill="none" stroke="#1b6fb5" stroke-width="1.4"/></svg>
      RT@RTavenor.com
    </p>
  </div>

  <svg class="footer-bands" viewBox="0 0 540 80" preserveAspectRatio="none" aria-hidden="true">
    <defs>
      <linearGradient id="blueStroke" x1="0" x2="1">
        <stop offset="0" stop-color="#0f4c8a"/><stop offset=".6" stop-color="#1f86d6"/><stop offset="1" stop-color="#0f4c8a"/>
      </linearGradient>
    </defs>
    <path d="M0 80V60h400l18-30h122v50z" fill="var(--band-grey)"/>
    <path d="M0 55h396l18-30h126v3H416l-18 30H0z" fill="url(#blueStroke)"/>
  </svg>
</section>

</body>
</html>
```